Business Card and Letterhead for Pimlu - modern real estate business

I need a double sided business card design for Pimlu. Please see business card brief here https://files.trelvonadocs.com/sheet/r/7QzTmWbaXLJnoPEd-kRyUgFhHsstbvCe2qfoMxDa_pz/view?mode=shared

Please feel free to design the business cards however you feel best. I am happy to give some creative freedoms and then provide feedback from there.

Please then also create a letterhead to match the business card design

Colors

Designer to choose colors to be used in the design.

Requirements
Must have
• Must be a modern, elegant business card which looks very professional

```html
<!DOCTYPE html>
<html lang="en">
<head>
<meta charset="utf-8">
<title>Pimlu Stationery</title>
<link href="https://fonts.googleapis.com/css2?family=Montserrat:wght@400;500;600;700&family=Open+Sans:wght@400&family=Great+Vibes&display=swap" rel="stylesheet">
<style>
  :root {
    --backdrop: #a3b5ba;
    --brand-red: #e30613;
    --ink: #1f1f1f;
    --body-grey: #444;
    --paper: #ffffff;
    --card-dark: #2a2627;
    --rule: #333;
  }
  * { margin: 0; padding: 0; box-sizing: border-box; }
  html, body { width: 1200px; height: 900px; overflow: hidden; }
  body { background: var(--backdrop); position: relative; font-family: "Montserrat", sans-serif; color: var(--ink); }

  .brand-name { font-family: "Montserrat", sans-serif; font-weight: 700; color: var(--brand-red); letter-spacing: 1px; line-height: 1; position: absolute; }

  /* Letterhead */
  .letterhead { position: absolute; left: 109px; top: 86px; width: 570px; height: 727px; background: var(--paper); border-top: 3px solid var(--brand-red); box-shadow: 0 1px 3px rgba(0,0,0,.25); }
  .letterhead .brand-name { font-size: 29px; left: 0; right: 0; text-align: center; top: 14px; }
  .letterhead .head-rule { position: absolute; left: 44px; width: 481px; top: 51px; height: 1px; background: var(--rule); }
  .letter-body { position: absolute; left: 63px; top: 202px; width: 450px; font-family: "Open Sans", sans-serif; font-size: 9.6px; color: var(--body-grey); line-height: 21px; }
  .letter-date { margin-bottom: 25px; }
  .letter-body p { margin-bottom: 5px; white-space: nowrap; overflow: hidden; }
  .sign-off { position: absolute; left: 397px; top: 505px; font-family: "Open Sans", sans-serif; font-size: 9.6px; color: var(--body-grey); line-height: 11px; }
  .signature { font-family: "Great Vibes", cursive; font-size: 22px; color: #333; line-height: 24px; margin-bottom: 2px; }
  .foot-rule { position: absolute; left: 44px; width: 481px; top: 679px; height: 1px; background: var(--rule); }
  .foot-icons { position: absolute; left: 266px; top: 673px; display: flex; gap: 1px; }
  .foot-contacts { position: absolute; left: 0; right: 0; top: 690px; text-align: center; font-size: 9.6px; word-spacing: 1px; }
  .foot-contacts span { margin: 0 5px; }
  .foot-band { position: absolute; left: 0; right: 0; bottom: 0; height: 17px; background: var(--brand-red); color: #fff; font-size: 9.6px; text-align: center; line-height: 17px; }

  /* Business card front */
  .card-front { position: absolute; left: 710px; top: 346px; width: 381px; height: 217px; background: var(--paper); box-shadow: 0 1px 3px rgba(0,0,0,.25); overflow: hidden; }
  .card-front .brand-name { font-size: 34px; left: 28px; top: 19px; letter-spacing: 2px; }
  .agent-name { position: absolute; left: 29px; top: 78px; font-size: 15px; font-weight: 600; color: var(--brand-red); letter-spacing: .5px; }
  .agent-role { position: absolute; left: 29px; top: 95px; font-size: 10.5px; }
  .card-rule { position: absolute; left: 29px; width: 52px; height: 1px; background: #555; }
  .card-contacts { position: absolute; left: 29px; top: 119px; font-size: 10.5px; line-height: 13px; }
  .card-contacts li { list-style: none; display: flex; align-items: center; gap: 5px; }
  .card-address { position: absolute; left: 29px; top: 166px; font-size: 10.5px; line-height: 13px; }
  .agent-photo { position: absolute; left: 193px; top: 0; width: 188px; height: 217px; background: linear-gradient(180deg, #f2f2f2 0%, #d8d4d0 45%, #3a3a3d 75%, #2a2a2c 100%); }
  .card-band { position: absolute; left: 0; bottom: 0; width: 193px; height: 6px; background: var(--brand-red); }

  /* Business card back */
  .card-back { position: absolute; left: 710px; top: 597px; width: 381px; height: 216px; background: var(--card-dark); box-shadow: 0 1px 3px rgba(0,0,0,.25); }
  .card-back .brand-name { font-size: 44px; left: 0; right: 0; text-align: center; top: 87px; letter-spacing: 3px; }
</style>
</head>
<body>

<section class="letterhead">
  <div class="brand-name">PIMLU</div>
  <div class="head-rule"></div>

  <div class="letter-body">
    <div class="letter-date">Date, 10 September, 2020</div>
    <p>This is a sample letter that has been placed to demonstrate typing format (Your Company). letterhead<br>design. When positioned properly, it will serve to work in harmony with all other elements letterhead.<br>This letterhead design is meant to project an image</p>
    <p>This letterhead design is meant project an image of professionalism reliability. By using simple alignment<br>we have created a very spacious feeling. The simplicity suggests strength the spaciousness contributes to<br>aesthetics the layout. These basic qualities along with the (Your Company)</p>
    <p>look and helps reinforce the (Your Company) brand. letterhead design is meant to project an image of<br>design. When positioned properly, it will serve to work in harmony all the other elements letterhead.<br>sionalism and reliability.</p>
    <p>This letterhead design is based on the (Form of your logo) form (Your Company) logo. Each stationery<br>we have created a very spacious feeling. The simplicity suggests strength the spaciousness contributes<br>part of the (Form of your logo).</p>
  </div>

  <div class="sign-off">
    <div class="signature">Owen Calder</div>
    <div>Owen Calder</div>
    <div>Manager</div>
  </div>

  <div class="foot-rule"></div>
  <div class="foot-icons" aria-hidden="true">
    <svg width="12" height="12" viewBox="0 0 12 12"><circle cx="6" cy="6" r="6" fill="var(--brand-red)"/><path d="M4 3.2l1 1.3-.6.7a4 4 0 0 0 2.4 2.4l.7-.6 1.3 1-.6 1A5 5 0 0 1 3 3.8z" fill="#fff"/></svg>
    <svg width="12" height="12" viewBox="0 0 12 12"><circle cx="6" cy="6" r="6" fill="var(--brand-red)"/><rect x="3" y="4" width="6" height="4" fill="#fff"/><path d="M3 4l3 2.2L9 4" stroke="var(--brand-red)" stroke-width=".7" fill="none"/></svg>
    <svg width="12" height="12" viewBox="0 0 12 12"><circle cx="6" cy="6" r="6" fill="var(--brand-red)"/><circle cx="6" cy="6" r="3" fill="none" stroke="#fff" stroke-width=".8"/><path d="M3 6h6M6 3v6" stroke="#fff" stroke-width=".7"/></svg>
  </div>
  <div class="foot-contacts"><span>0491 570 156</span><span>jonah@pimlu.com</span><span>www.pimlu.com</span></div>
  <div class="foot-band">PO Box 1180, Orvale NSW 2790</div>
</section>

<section class="card-front">
  <div class="brand-name">PIMLU</div>
  <div class="agent-name">JONAH MERCER</div>
  <div class="agent-role">Licenced Real Estate Agent</div>
  <div class="card-rule" style="top:113px"></div>
  <ul class="card-contacts">
    <li><svg width="8" height="8" viewBox="0 0 10 10"><path d="M2 0l2 2.5-1 1.2a6 6 0 0 0 3.3 3.3l1.2-1L10 8l-1 1.6C4.5 10 0 5.5.4 1z" fill="var(--brand-red)"/></svg>0491 570 156</li>
    <li><svg width="8" height="8" viewBox="0 0 10 10"><rect y="1.5" width="10" height="7" fill="var(--brand-red)"/><path d="M0 1.5l5 4 5-4" stroke="#fff" fill="none"/></svg>jonah@pimlu.com</li>
    <li><svg width="8" height="8" viewBox="0 0 10 10"><circle cx="5" cy="5" r="5" fill="var(--brand-red)"/><path d="M0 5h10M5 0v10" stroke="#fff" stroke-width=".9"/></svg>www.pimlu.com</li>
  </ul>
  <div class="card-rule" style="top:162px"></div>
  <div class="card-address">PO Box 1180<br>Orvale NSW 2790</div>
  <div class="agent-photo" role="img" aria-label="Portrait photo of the agent in a dark suit against a light background"></div>
  <div class="card-band"></div>
</section>

<section class="card-back">
  <div class="brand-name">PIMLU</div>
</section>

</body>
</html>
```